Business card for law firm

Need business card for new law firm. Think confident, authoritative, conservative, but not stuffy or old-fashioned.

Contact Information for Business Card

Content for card - logo (uploaded), plus the following:

Paul Whitcombe (larger font)
Managing Partner (larger font, but not as large as name)
Level 9, 7 Ferris Lane
Sydney NSW 2000
Main Tel 02 9364 2710
Direct Tel 02 8472 3159
Email paul@qvlegal.com.au
www.qvlegal.com.au

Letterhead design should include logo plus:
Level 9, 7 Ferris Lane
Sydney NSW 2000
Tel 02 8472 3159
www.qvlegal.com.au

```html
<!DOCTYPE html>
<html lang="en">
<head>
<meta charset="utf-8">
<title>Quayvale Legal – Business Card</title>
<link rel="stylesheet" href="https://fonts.googleapis.com/css2?family=Cormorant+Garamond:wght@600&family=Open+Sans:wght@400;700&display=swap">
<style>
  :root {
    --backdrop: #7d7d7d;
    --card: #f7f7f5;
    --navy: #14235e;
    --ink: #1e1e1e;
    --ink-soft: #3a3a3a;
  }
  html, body {
    margin: 0;
    width: 1200px;
    height: 848px;
    overflow: hidden;
    background: var(--backdrop);
  }
  .canvas {
    position: relative;
    width: 1200px;
    height: 848px;
  }
  .card {
    position: absolute;
    top: 272px;
    width: 500px;
    height: 304px;
    background: var(--card);
    box-shadow: 0 10px 24px rgba(0,0,0,0.28);
    box-sizing: border-box;
  }
  .card--contact { left: 70px; }
  .card--brand { left: 630px; }

  /* Contact side */
  .contact-mark {
    position: absolute;
    left: 46px;
    top: 52px;
    width: 128px;
    height: 128px;
    background: var(--navy);
  }
  .contact-details {
    position: absolute;
    left: 198px;
    top: 56px;
    font-family: "Open Sans", Arial, sans-serif;
    color: var(--ink-soft);
  }
  .contact-name {
    margin: 0;
    font-size: 25px;
    font-weight: 700;
    line-height: 1.05;
    color: var(--navy);
  }
  .contact-role {
    margin: 0 0 12px;
    font-size: 17px;
    font-weight: 700;
    line-height: 1.2;
    color: var(--ink);
  }
  .contact-lines {
    margin: 0;
    padding: 0;
    list-style: none;
    font-size: 13px;
    line-height: 1.45;
  }
  .contact-web {
    margin: 6px 0 0;
    font-size: 14px;
    font-weight: 700;
    color: var(--ink);
  }

  /* Brand side */
  .brand-lockup {
    position: absolute;
    inset: 0;
    display: flex;
    align-items: center;
    justify-content: center;
    gap: 18px;
  }
  .brand-square {
    width: 34px;
    height: 34px;
    background: var(--navy);
  }
  .brand-name {
    margin: 0;
    font-family: "Cormorant Garamond", Georgia, serif;
    font-weight: 600;
    font-size: 38px;
    letter-spacing: 4px;
    text-transform: uppercase;
    color: var(--ink);
  }
</style>
</head>
<body>
<main class="canvas">
  <section class="card card--contact" aria-label="Business card, contact side">
    <div class="contact-mark"></div>
    <div class="contact-details">
      <h1 class="contact-name">Paul Whitcombe</h1>
      <p class="contact-role">Managing Partner</p>
      <ul class="contact-lines">
        <li>Level 9, 7 Ferris Lane</li>
        <li>Sydney NSW 2000</li>
        <li>02 9364 2710 (Main)</li>
        <li>02 8472 3159 (Direct)</li>
        <li>paul@qvlegal.com.au</li>
      </ul>
      <p class="contact-web">www.qvlegal.com.au</p>
    </div>
  </section>

  <section class="card card--brand" aria-label="Business card, brand side">
    <div class="brand-lockup">
      <div class="brand-square"></div>
      <p class="brand-name">Quayvale Legal</p>
    </div>
  </section>
</main>
</body>
</html>
```